Corvane Freight Company Business Card Design

We are a company that delivers natural saltwater (from the ocean) to aquarium companies, restaurants and home marine tanks. I would like a new business card to suit.

Must include Name, company name, abn, contact number and website as well as logo (see attached).

Looking for a design that stands out, has a clean but unique appearance.

Double and single sided entries welcome

Business

• Logo

```html
<!DOCTYPE html>
<html lang="en">
<head>
<meta charset="utf-8">
<title>Corvane Freight Company – Business Card</title>
<link rel="stylesheet" href="https://fonts.googleapis.com/css2?family=Jost:wght@400;500;700&display=swap">
<style>
  :root {
    --backdrop: #2b2b2d;
    --front-blue: #2c6fe6;
    --back-blue: #3db0f2;
    --band-cyan: #b8f1fb;
    --band-light: #c9f6fd;
    --divider-cyan: #7fdcf5;
    --white: #ffffff;
    --ink: #1d3557;
  }
  * { margin: 0; padding: 0; box-sizing: border-box; }
  html, body {
    width: 1200px;
    height: 980px;
    overflow: hidden;
    background: var(--backdrop);
    font-family: "Jost", "Helvetica Neue", Arial, sans-serif;
  }
  .canvas { position: relative; width: 1200px; height: 980px; }

  .card {
    position: absolute;
    width: 694px;
    height: 396px;
    overflow: hidden;
    color: var(--white);
  }
  .card--front { left: 87px; top: 61px; background: var(--front-blue); }
  .card--back { left: 400px; top: 514px; background: var(--back-blue); }

  .holder {
    position: absolute;
    top: 10px; left: 0; right: 0;
    text-align: center;
    font-size: 24px;
    font-weight: 700;
  }
  .holder__title { font-weight: 400; font-size: 22px; }

  .brand-name {
    position: absolute;
    left: 0; right: 0;
    text-align: center;
    font-weight: 700;
    color: var(--white);
    line-height: 1;
  }
  .card--front .brand-name { top: 128px; font-size: 50px; }
  .card--back .brand-name { top: 160px; font-size: 50px; }

  .contact-company {
    position: absolute;
    right: 352px;
    top: 270px;
    text-align: right;
    font-size: 17px;
    line-height: 21px;
  }
  .contact-company__name { font-size: 20px; line-height: 24px; }
  .contact-divider {
    position: absolute;
    left: 361px; top: 262px;
    width: 2px; height: 82px;
    background: var(--divider-cyan);
  }
  .contact-lines {
    position: absolute;
    left: 380px; top: 274px;
    font-size: 19px;
    line-height: 30px;
  }
  .contact-lines__phone { display: flex; align-items: center; gap: 6px; }
  .contact-lines__phone svg { width: 15px; height: 15px; }

  .footer-band { position: absolute; left: 0; bottom: 0; width: 694px; height: 30px; }
  .footer-web {
    position: absolute;
    right: 74px; bottom: 4px;
    font-size: 18px;
    letter-spacing: 3px;
    color: var(--ink);
  }

  .back-web {
    position: absolute;
    left: 0; right: 0; top: 300px;
    text-align: center;
    font-size: 21px;
    letter-spacing: 4px;
  }
</style>
</head>
<body>
<main class="canvas">

  <section class="card card--front" aria-label="Card front">
    <p class="holder">Your name, <span class="holder__title">Title</span></p>

    <p class="brand-name">Corvane Freight</p>

    <div class="contact-company">
      <p class="contact-company__name">Corvane Freight Company</p>
      <p>Street Name, City Name</p>
      <p>State, City Zip Code</p>
    </div>
    <div class="contact-divider"></div>
    <div class="contact-lines">
      <p class="contact-lines__phone">
        <svg viewBox="0 0 16 16" aria-hidden="true">
          <circle cx="8" cy="8" r="7" fill="none" stroke="#ffffff" stroke-width="1.4"/>
          <path d="M5.2 4.5 L6.6 4.3 L7.2 6.2 L6.3 6.9 Q7 8.6 8.9 9.6 L9.7 8.8 L11.5 9.4 L11.3 10.9 Q7.8 11.2 5.2 4.5 Z" fill="#ffffff"/>
        </svg>
        123-456-7890
      </p>
      <p>ABN : 0123456789</p>
    </div>

    <svg class="footer-band" viewBox="0 0 694 30" aria-hidden="true">
      <polygon points="0,0 336,0 318,30 0,30" fill="var(--band-cyan)"/>
      <polygon points="336,0 357,0 339,30 318,30" fill="var(--front-blue)"/>
      <polygon points="357,0 694,0 694,30 339,30" fill="var(--band-light)"/>
    </svg>
    <p class="footer-web">www.website.com</p>
  </section>

  <section class="card card--back" aria-label="Card back">
    <p class="brand-name">Corvane Freight</p>
    <p class="back-web">www.website.com</p>
  </section>

</main>
</body>
</html>
```